Wordpress theme website for professionals working together

My partner and I are offering business services, my wife in the energy business as mainly as member of the board of commissioners. I am working as interim manager/consultant in the accounting and finance area. Both activities are connected in one company VELMOT BV (dutch ltd). We need a CV based website. Beside this we do some financial and accounting services.

Target Market(s)

small medium business

Font styles to use
Sans Serif

Colors

Designer to choose colors to be used in the design.

Requirements
Must have
• Pictures of both members.
• CLEAN AND SIMPLE
• I LIKE BLACK & WHITE
Nice to have
• I like design like this theme: http://theme.pruxelo-example.com/resume/

```html
<!DOCTYPE html>
<html lang="en">
<head>
<meta charset="utf-8">
<title>VELMOT BV – Resume</title>
<link href="https://fonts.googleapis.com/css2?family=Mulish:wght@300;400;600;700;800&display=swap" rel="stylesheet">
<style>
:root{
  --ink:#1f1f1f;
  --text:#444;
  --muted:#666;
  --white:#fff;
  --panel:#efefef;
  --dark:#141414;
  --track:#8a8a8a;
  --fill:#e6e6e6;
  --line:#cfcfcf;
}
*{box-sizing:border-box;margin:0;padding:0}
html,body{width:1200px;height:3297px;overflow:hidden}
body{font-family:"Mulish",Arial,sans-serif;color:var(--ink);background:var(--white);position:relative}
.section{position:absolute;left:0;width:1200px}
.abs{position:absolute}

/* header */
.site-header{top:0;height:81px;background:var(--white)}
.brand{font-weight:800;font-size:31px;letter-spacing:-.5px;color:var(--ink)}
.site-header .brand{left:166px;top:20px}
.main-nav{left:417px;top:28px;display:flex;gap:37px;font-size:17px;color:var(--text)}

/* hero */
.hero{top:81px;height:574px;background:linear-gradient(90deg,#e3e7ee 0%,#d6dbe3 50%,#c9ced6 100%);overflow:hidden}
.hero-photo{right:0;top:0;width:720px;height:574px;background:radial-gradient(ellipse 45% 60% at 62% 45%,#c9a493 0%,#a27f72 35%,#6d6b72 65%,rgba(214,219,227,0) 100%)}
.hero-name{left:166px;top:118px;font-size:74px;font-weight:700;letter-spacing:-1px}
.hero-role{left:168px;top:203px;font-size:28px;font-weight:700;color:#333}
.hero-text{left:168px;top:253px;width:388px;font-size:15px;line-height:24px;color:var(--text)}
.cta-pill{left:205px;top:364px;width:160px;height:50px;border-radius:25px;background:#111;color:var(--white);font-size:17px;font-weight:700;padding:15px 0 0 52px}
.cta-avatar{left:168px;top:352px;width:78px;height:78px;border-radius:50%;border:3px solid var(--white);background:radial-gradient(circle at 50% 45%,#c99a83 0%,#7a5a4d 55%,#3a2e2a 100%)}
.cta-name{left:186px;top:436px;font-size:16px;font-weight:700}

/* jobs */
.jobs{top:655px;height:497px;background:var(--white)}
.jobs-finished{left:600px;top:0;width:600px;height:497px;background:var(--panel)}
.col-title{font-size:28px;font-weight:600}
.job h3{font-size:18px;font-weight:700;margin-bottom:8px}
.job p{font-size:15px;line-height:22px;color:var(--muted)}

/* skills */
.skills{top:1152px;height:562px;background:radial-gradient(ellipse at 50% 50%,#2a2a2a 0%,var(--dark) 75%)}
.section-title{width:1200px;text-align:center;font-weight:400}
.skills .section-title{top:52px;font-size:44px;color:var(--white)}
.skill{width:368px;color:var(--white)}
.skill-name{font-size:18px;font-weight:700}
.skill-pct{position:absolute;right:10px;top:6px;font-size:14px;font-weight:600}
.skill-track{position:absolute;left:0;top:30px;width:368px;height:7px;border-radius:4px;background:var(--track)}
.skill-fill{height:7px;border-radius:4px;background:var(--fill)}

/* education */
.education{top:1714px;height:414px;background:linear-gradient(135deg,#f1f1f1,#dcdcdc)}
.education .section-title{top:60px;font-size:38px;color:var(--ink)}
.edu-card{top:139px;width:394px;height:165px;border-radius:70px;background:var(--white);border:2px solid var(--line);text-align:center;padding-top:24px}
.edu-card h3{font-size:24px;font-weight:400;margin-bottom:12px}
.edu-card p{font-size:14px;line-height:21px;color:var(--text);width:290px;margin:0 auto}

/* photos */
.gallery{top:2128px;height:558px;background:var(--white)}
.gallery .section-title{top:36px;font-size:38px}
.photo-grid{left:160px;top:112px;width:880px;display:grid;grid-template-columns:repeat(4,217px);grid-auto-rows:176px;gap:4px}

/* contact */
.contact{top:2686px;height:475px;background:linear-gradient(180deg,#2e2e2e,#242424)}
.contact-title{left:158px;top:82px;font-size:38px;font-weight:400;color:var(--white)}
.contact-text{left:158px;top:140px;width:330px;font-size:16px;line-height:23px;color:#ddd}
.contact-line{left:158px;display:flex;align-items:center;gap:12px;color:var(--white);font-size:19px}
.field{border:1.5px solid #9a9a9a;color:#ccc;font-size:13px;padding:10px 14px}
.send-btn{left:517px;top:297px;width:528px;height:46px;border:2px solid var(--white);color:var(--white);font-size:20px;font-weight:700;text-align:center;padding-top:9px;letter-spacing:1px}

/* footer */
.site-footer{top:3161px;height:136px;background:var(--white)}
.site-footer .brand{left:180px;top:40px;font-size:29px}
.footer-nav{left:395px;top:34px;display:flex;gap:30px;font-size:16px;color:var(--text)}
.copyright{left:398px;top:70px;font-size:13px;color:var(--muted)}
.social{left:905px;top:36px;display:flex;gap:24px}
.social span{width:16px;height:16px;border-radius:50%;background:var(--ink);display:block}
</style>
</head>
<body>

<header class="section site-header">
  <div class="abs brand">VELMOT BV</div>
  <nav class="abs main-nav"><span>Home</span><span>Jobs</span><span>Skills</span><span>Education</span><span>Worked</span><span>Other</span></nav>
</header>

<section class="section hero">
  <div class="abs hero-photo" role="img" aria-label="Portrait photograph of Hendrik, smiling man with glasses"></div>
  <h1 class="abs hero-name">Hendrik</h1>
  <div class="abs hero-role">Advisor TRV</div>
  <p class="abs hero-text">Morbi porta libero id ullamcorper nonummy nibh ligula pulvinar metus eget consectetuer augue nisi quis lacus Ut ac mi quis lacus mollis aliquam vvsceleri</p>
  <div class="abs cta-pill">Click here</div>
  <div class="abs cta-avatar" role="img" aria-label="Portrait photograph of partner Marit"></div>
  <div class="abs cta-name">Marit</div>
</section>

<section class="section jobs">
  <div class="abs jobs-finished"></div>
  <h2 class="abs col-title" style="left:166px;top:62px">Actual jobs</h2>
  <div class="abs job" style="left:166px;top:145px;width:410px">
    <h3>Advisor TRV</h3>
    <p>Morbi porta libero id ullamcorper nonummy nibh ligula pulvinar metus eget consectetuer augue nisi quis</p>
  </div>
  <div class="abs job" style="left:166px;top:283px;width:410px">
    <h3>Advisor How &amp;amp; knower</h3>
    <p>Morbi porta libero id ullamcorper nonummy nibh ligula pulvinar metus eget consectetuer augue nisi quis</p>
  </div>
  <h2 class="abs col-title" style="left:655px;top:62px">Finished jobs</h2>
  <div class="abs job" style="left:655px;top:149px;width:420px">
    <h3>Controller a.i. TRV</h3>
    <p>Morbi porta libero id ullamcorper nonummy nibh ligula pulvinar metus eget consectetuer augue nisi quis</p>
  </div>
  <div class="abs job" style="left:655px;top:270px;width:420px">
    <h3>Advisor Delta Fern</h3>
    <p>Morbi porta libero id ullamcorper nonummy nibh ligula</p>
  </div>
  <div class="abs job" style="left:655px;top:365px;width:420px">
    <h3>Financial director NLO</h3>
    <p>Morbi porta libero id ullamcorper nonummy nibh ligula</p>
  </div>
</section>

<section class="section skills">
  <h2 class="abs section-title">Skills</h2>
  <div class="abs skill" style="left:196px;top:146px"><div class="skill-name">Annual reporting</div><span class="skill-pct">85%</span><div class="skill-track"><div class="skill-fill" style="width:92%"></div></div></div>
  <div class="abs skill" style="left:624px;top:146px"><div class="skill-name">Project management</div><span class="skill-pct">70%</span><div class="skill-track"><div class="skill-fill" style="width:84%"></div></div></div>
  <div class="abs skill" style="left:196px;top:230px"><div class="skill-name">Financial monthly reporting</div><span class="skill-pct">66%</span><div class="skill-track"><div class="skill-fill" style="width:73%"></div></div></div>
  <div class="abs skill" style="left:624px;top:230px"><div class="skill-name">Team player</div><span class="skill-pct">77%</span><div class="skill-track"><div class="skill-fill" style="width:92%"></div></div></div>
  <div class="abs skill" style="left:196px;top:314px"><div class="skill-name">Accounting</div><span class="skill-pct">87%</span><div class="skill-track"><div class="skill-fill" style="width:91%"></div></div></div>
  <div class="abs skill" style="left:624px;top:314px"><div class="skill-name">Trouble shooter</div><span class="skill-pct">60%</span><div class="skill-track"><div class="skill-fill" style="width:66%"></div></div></div>
  <div class="abs skill" style="left:196px;top:398px"><div class="skill-name">Financial management</div><span class="skill-pct">80%</span><div class="skill-track"><div class="skill-fill" style="width:87%"></div></div></div>
  <div class="abs skill" style="left:624px;top:398px"><div class="skill-name">ETC</div><span class="skill-pct">72%</span><div class="skill-track"><div class="skill-fill" style="width:81%"></div></div></div>
</section>

<section class="section education">
  <h2 class="abs section-title">Education</h2>
  <div class="abs edu-card" style="left:187px">
    <h3>Kovra (RA)</h3>
    <p>Morbi porta libero id ullamcorper nonummy nibh ligula pulvinar metus eget consectetuer augue nisi quis lacus Ut ac mi</p>
  </div>
  <div class="abs edu-card" style="left:597px">
    <h3>Atheneum B</h3>
    <p>Morbi porta libero id ullamcorper nonummy nibh ligula pulvinar metus eget consectetuer augue nisi quis lacus Ut ac mi</p>
  </div>
</section>

<section class="section gallery">
  <h2 class="abs section-title">Fotography</h2>
  <div class="abs photo-grid">
    <div class="photo" role="img" aria-label="Sunlit forest photograph" style="background:linear-gradient(135deg,#d9b36a,#5a4a2e)"></div>
    <div class="photo" role="img" aria-label="Green meadow under blue sky photograph" style="background:linear-gradient(180deg,#8fbbe6 0%,#a7cf6a 45%,#4f8f2a 100%)"></div>
    <div class="photo" role="img" aria-label="Road through trees photograph" style="background:linear-gradient(180deg,#c9d6b0,#3f5a30 55%,#6b6b66)"></div>
    <div class="photo" role="img" aria-label="City skyscrapers photograph" style="background:linear-gradient(180deg,#b9c9dd,#4d5e77)"></div>
    <div class="photo" role="img" aria-label="City street at sunset photograph" style="background:linear-gradient(180deg,#a9b4cc,#e8cfa2 50%,#535a6a)"></div>
    <div class="photo" role="img" aria-label="Mountain valley landscape photograph" style="background:linear-gradient(180deg,#7f9a9c,#2f4a2a)"></div>
    <div class="photo" role="img" aria-label="Misty park with trees photograph" style="background:linear-gradient(180deg,#e9ecdc,#6c8a4a)"></div>
    <div class="photo" role="img" aria-label="Traveller on a hilltop photograph" style="background:linear-gradient(180deg,#e7d5c0,#7a6a5e 60%,#b7855f)"></div>
  </div>
</section>

<section class="section contact" role="img" aria-label="Dark desk workspace background photograph">
  <h2 class="abs contact-title">Contact</h2>
  <p class="abs contact-text">blandit sed nulla In ullamcorper est eget tempor cursus neque mi consectetuer mi a ultricies massa est sed nisl Class aptent taciti sociosqu ad litora torquent per</p>
  <div class="abs contact-line" style="top:272px">
    <svg width="18" height="18" viewBox="0 0 24 24"><path fill="#fff" d="M6.6 10.8a15 15 0 0 0 6.6 6.6l2.2-2.2a1 1 0 0 1 1-.25 11.4 11.4 0 0 0 3.6.57 1 1 0 0 1 1 1V20a1 1 0 0 1-1 1A17 17 0 0 1 3 4a1 1 0 0 1 1-1h3.5a1 1 0 0 1 1 1c0 1.25.2 2.45.57 3.57a1 1 0 0 1-.25 1z"/></svg>
    <span>555.014.2290</span>
  </div>
  <div class="abs contact-line" style="top:302px">
    <svg width="20" height="16" viewBox="0 0 20 16"><rect x="1" y="1" width="18" height="14" fill="none" stroke="#fff" stroke-width="2"/><path d="M1 1l9 7 9-7" fill="none" stroke="#fff" stroke-width="2"/></svg>
    <span>info@velmot-example.com</span>
  </div>
  <div class="abs field" style="left:512px;top:103px;width:264px;height:40px">Name</div>
  <div class="abs field" style="left:784px;top:103px;width:262px;height:40px">Email address</div>
  <div class="abs field" style="left:512px;top:152px;width:534px;height:126px">Message</div>
  <div class="abs send-btn">SEND</div>
</section>

<footer class="section site-footer">
  <div class="abs brand">VELMOT BV</div>
  <nav class="abs footer-nav"><span>Home</span><span>Jobs</span><span>Skills</span><span>Education</span><span>Worked</span><span>Other</span></nav>
  <div class="abs copyright">© 2018 Company Name  All right reserved</div>
  <div class="abs social" aria-label="Social links"><span></span><span></span><span></span><span></span></div>
</footer>

</body>
</html>
```